A Health & Fitness Website selling saunas and Cold tubs

www.dockvaultguys.com, www.frostlanterguys, www.chillharborguys
Design a website
We are selling saunas, infrared saunas, cold plunge tubs, and massage chairs to financially successful MEN.
We want professional, simple, masculine with a touch of sexy.
One section for each… saunas, cold plunge tubs, massage chairs.
Each will have at least two buy links to their affiliate/supplier/store.
The landing page / opening page / needs big & bold; a full screen image? a great picture showing the warmth of a sauna? Need your ideas
The pictures are everything.

The Website for our book
https://maebelsvigorguys.com/

Coding

Coded - Design and coding required

Number of Pages Required

1 page

Requirements
Must have
• Great pictures

```html
<!DOCTYPE html>
<html lang="en">
<head>
<meta charset="utf-8">
<title>Maebel Stone Vigor — Saunas, Cold Plunge Tubs &amp; Massage Chairs</title>
<link rel="stylesheet" href="https://fonts.googleapis.com/css2?family=Roboto+Condensed:wght@500;700&family=Roboto:wght@400;500;700&display=swap">
<style>
:root{
  --orange:#e8501f;
  --dark:#1f1f1f;
  --ink:#222;
  --muted:#6b6b6b;
  --grey:#efefef;
  --white:#fff;
  --head:"Roboto Condensed",sans-serif;
  --body:"Roboto",sans-serif;
}
*{box-sizing:border-box;margin:0;padding:0}
html,body{width:1200px;height:4785px;overflow:hidden}
body{position:relative;background:var(--white);font-family:var(--body);color:var(--ink)}
.abs{position:absolute}
.btn{position:absolute;display:flex;align-items:center;justify-content:center;gap:10px;height:40px;border-radius:20px;font:700 14px var(--body);color:var(--white);text-transform:uppercase;letter-spacing:.2px}
.btn .dot{width:13px;height:13px;border-radius:50%;background:var(--white);position:relative}
.btn .dot::after{content:"";position:absolute;left:4px;top:3.5px;border-left:5px solid currentColor;border-top:3px solid transparent;border-bottom:3px solid transparent}
.btn-orange{background:var(--orange)}
.btn-orange .dot::after{border-left-color:var(--orange)}
.btn-dark{background:var(--dark)}
.btn-dark .dot::after{border-left-color:var(--dark)}

/* header */
.site-header{position:absolute;left:0;top:0;width:1200px;height:98px;background:var(--white);z-index:2}
.brand{position:absolute;left:110px;top:0;width:178px;height:172px;border-radius:50%;background:var(--white);display:flex;align-items:center;justify-content:center;text-align:center;z-index:3;box-shadow:0 2px 6px rgba(0,0,0,.15)}
.brand span{font:700 22px/1.1 var(--head);color:var(--ink);text-transform:uppercase;width:120px}
.nav{position:absolute;top:43px;left:450px;display:flex;gap:0;font:500 15px var(--body);text-transform:uppercase;color:var(--ink)}
.nav a{color:inherit;text-decoration:none}
.nav .sep{margin:0 26px}

/* hero */
.hero{position:absolute;left:0;top:98px;width:1200px;height:731px;background:radial-gradient(ellipse at 70% 35%,#9a7a3a 0%,#4a3a1e 35%,#1a1f14 65%),#1a1a12}
.hero-glow{position:absolute;left:0;bottom:0;width:1200px;height:360px;background:radial-gradient(ellipse at 30% 80%,rgba(30,170,90,.75),rgba(10,60,30,0) 70%)}
.hero h1{position:absolute;left:0;top:388px;width:1200px;text-align:center;font:700 74px/76px var(--head);color:var(--white);text-transform:uppercase;text-shadow:0 3px 8px rgba(0,0,0,.5)}

/* products */
.section-title{position:absolute;left:0;width:1200px;text-align:center;font:700 40px var(--head);text-transform:uppercase;color:var(--ink)}
.product-photo{position:absolute;width:412px;height:287px;border-radius:4px}
.product-copy{position:absolute;width:475px}
.product-copy h3{font:500 30px var(--body);color:var(--ink);margin-bottom:12px}
.product-copy h4{font:500 14px var(--body);margin-bottom:10px}
.product-copy p{font:400 13px/26px var(--body);color:var(--muted);text-align:justify}

/* bands */
.intro-band{position:absolute;left:0;top:2140px;width:1200px;height:298px;background:var(--grey);text-align:center}
.intro-band .kicker{font:500 14px/26px var(--body);margin-top:48px}
.intro-band h2{font:700 38px/45px var(--head);text-transform:uppercase;margin:18px 0 14px}
.intro-band p{font:400 14px var(--body)}
.orange-band{position:absolute;left:0;width:1200px;background:var(--orange);display:flex;align-items:center;justify-content:center;text-align:center;font:700 38px/44px var(--head);color:var(--white);text-transform:uppercase}

/* benefits */
.benefits-title{position:absolute;left:0;top:2763px;width:1200px;text-align:center;font:700 38px/48px var(--head);text-transform:uppercase}
.benefit{position:absolute;width:223px;height:231px;background:var(--white);box-shadow:0 3px 12px rgba(0,0,0,.12);text-align:center}
.benefit .icon{width:88px;height:88px;border-radius:50%;background:var(--orange);margin:38px auto 24px}
.benefit span{font:500 17px/27px var(--body);text-transform:uppercase;display:block;padding:0 18px}
.benefit.active{background:var(--orange);color:var(--white)}
.benefit.active .icon{background:var(--white)}
.individual{position:absolute;left:0;top:3488px;width:1200px;text-align:center;font:500 34px var(--head)}

/* testimonials */
.quote{position:absolute;top:4060px;height:228px;background:var(--white);border-radius:10px;box-shadow:0 3px 12px rgba(0,0,0,.13);padding:38px 22px 0}
.quote::after{content:"";position:absolute;left:50%;bottom:-12px;margin-left:-12px;border-top:12px solid var(--white);border-left:12px solid transparent;border-right:12px solid transparent}
.quote p{font:400 13px/25.5px var(--body);color:var(--muted);text-align:justify}
.qmark{position:absolute;font:700 30px/1 var(--head);color:var(--orange)}
.stars{position:absolute;top:4310px;font-size:16px;color:#e7b712;letter-spacing:1px;text-align:center}
.arrow{position:absolute;top:4170px}

/* footer */
.site-footer{position:absolute;left:0;top:4418px;width:1200px;height:367px;background:#1e1e1e;color:var(--white)}
.foot-brand{position:absolute;left:138px;top:62px;width:140px;height:140px;border-radius:50%;background:#2e2e2e;border:2px solid #fff;display:flex;align-items:center;justify-content:center;text-align:center;font:700 18px/1.1 var(--head);text-transform:uppercase}
.socials{position:absolute;left:135px;top:230px;display:flex;gap:7px}
.socials i{width:31px;height:31px;border-radius:50%;background:var(--white)}
.foot-col{position:absolute;top:52px}
.foot-col h5{font:700 17px var(--body);margin-bottom:20px}
.foot-col li{list-style:none;font:400 13px var(--body);margin-bottom:19px;padding-left:22px;position:relative}
.foot-col li::before{content:"»";position:absolute;left:0;top:-1px;color:var(--orange);font-weight:700}
.contact-line{font:400 13px/22px var(--body);padding-left:28px;position:relative;margin-bottom:20px}
.contact-line svg{position:absolute;left:0;top:4px}
.foot-rule{position:absolute;left:111px;top:298px;width:978px;height:1px;background:#444}
.copyright{position:absolute;left:0;top:322px;width:1200px;text-align:center;font:400 13px var(--body)}
</style>
</head>
<body>

<header class="site-header">
  <nav class="nav">
    <a href="#">Home</a><span class="sep">|</span>
    <a href="#">About Us</a><span class="sep">|</span>
    <a href="#">Products</a><span class="sep">|</span>
    <a href="#">ContactUs</a>
  </nav>
  <a class="btn btn-orange" style="left:940px;top:33px;width:145px">Buy Now <span class="dot"></span></a>
</header>
<div class="brand"><span>Maebel Stone Vigor</span></div>

<section class="hero">
  <div role="img" aria-label="Couple relaxing in a warm, candle-lit hot tub with green-lit water" style="position:absolute;inset:0"></div>
  <div class="hero-glow"></div>
  <h1>Helping Guys Get Hot,<br>Sweaty&amp;Hard</h1>
  <a class="btn btn-orange" style="left:522px;top:566px;width:154px">Get Started <span class="dot"></span></a>
</section>

<h2 class="section-title" style="top:926px">Our Products</h2>

<div class="product-photo" role="img" aria-label="Wooden sauna interior with heater stones and bucket" style="left:121px;top:1025px;background:linear-gradient(135deg,#7a3f17,#c07a3a 55%,#4a2510)"></div>
<div class="product-copy" style="left:604px;top:1038px">
  <h3>Saunas</h3>
  <h4>Lorem ipsum dolor sit amet, consectetur adipis</h4>
  <p>Lorem ipsum dolor sit amet, consectetur adipiscing elit, sed do eiusmod tempor incididunt ut labore et dolore magna aliqua. Ut enim ad minim veniam, quis nostrud exercitation ullamco laboris nisi ut aliquip ex ea commodo consequat. Duis aute irure dolor in reprehenderit in voluptate velit esse cillum dolore co laboris nisi aliquip&nbsp; commodo consequat.</p>
</div>
<a class="btn btn-orange" style="left:604px;top:1254px;width:155px">Buy Now <span class="dot"></span></a>
<a class="btn btn-dark" style="left:773px;top:1254px;width:181px">Contact Store <span class="dot"></span></a>

<div class="product-copy" style="left:121px;top:1404px">
  <h3>Cold Plunge Tubs</h3>
  <h4>Lorem ipsum dolor sit amet, consectetur adipis</h4>
  <p>Lorem ipsum dolor sit amet, consectetur adipiscing elit, sed do eiusmod tempor incididunt ut labore et dolore magna aliqua. Ut enim ad minim veniam, quis nostrud exercitation ullamco laboris nisi ut aliquip ex ea commodo consequat. Duis aute irure dolor in reprehenderit in voluptate velit esse cillum dolore co laboris nisi aliquip&nbsp; commodo consequat.</p>
</div>
<a class="btn btn-orange" style="left:121px;top:1620px;width:155px">Buy Now <span class="dot"></span></a>
<a class="btn btn-dark" style="left:290px;top:1620px;width:181px">Contact Store <span class="dot"></span></a>
<div class="product-photo" role="img" aria-label="Person bathing in an outdoor cold plunge tub in winter" style="left:667px;top:1392px;background:linear-gradient(135deg,#dfe4ea,#9aa3ad 50%,#4d4640)"></div>

<div class="product-photo" role="img" aria-label="Row of black and white massage chairs in a showroom" style="left:121px;top:1758px;background:linear-gradient(135deg,#e6e6e2,#8d8d88 50%,#2a2a2a)"></div>
<div class="product-copy" style="left:604px;top:1770px">
  <h3>Massage Chairs</h3>
  <h4>Lorem ipsum dolor sit amet, consectetur adipis</h4>
  <p>Lorem ipsum dolor sit amet, consectetur adipiscing elit, sed do eiusmod tempor incididunt ut labore et dolore magna aliqua. Ut enim ad minim veniam, quis nostrud exercitation ullamco laboris nisi ut aliquip ex ea commodo consequat. Duis aute irure dolor in reprehenderit in voluptate velit esse cillum dolore co laboris nisi aliquip&nbsp; commodo consequat.</p>
</div>
<a class="btn btn-orange" style="left:604px;top:1986px;width:155px">Buy Now <span class="dot"></span></a>
<a class="btn btn-dark" style="left:773px;top:1986px;width:181px">Contact Store <span class="dot"></span></a>

<section class="intro-band">
  <p class="kicker">Maebel Stone Vigor for Men<br>Top of the Line Health Products Exclusively for the Financially Successful</p>
  <h2>Dramatically Improve Your Health<br>Without Exercise</h2>
  <p>Successful Men Recognize the Importance of Their Health and Make it a Priority.&nbsp; It's Your Time.&nbsp; You've Earned it</p>
</section>

<section class="orange-band" style="top:2438px;height:247px">A Mans Body Thrives on Circulation<br>and It Doesn't Care How You Get It</section>

<h2 class="benefits-title">When There's No Time for Exercise.<br>Use Hot, Cold, or Massage.<br>The Benefits Are Numerous.</h2>

<div class="benefit" style="left:111px;top:2941px"><div class="icon" role="img" aria-label="Stress relief icon"></div><span>Relieve Stress</span></div>
<div class="benefit" style="left:362px;top:2941px"><div class="icon" role="img" aria-label="Detox icon"></div><span>Detox Your Pores</span></div>
<div class="benefit active" style="left:615px;top:2941px"><div class="icon" role="img" aria-label="Sleep icon"></div><span>Sleep Better</span></div>
<div class="benefit" style="left:866px;top:2941px"><div class="icon" role="img" aria-label="Muscle icon"></div><span>Relieve Muscle Tension</span></div>
<div class="benefit" style="left:111px;top:3216px"><div class="icon" role="img" aria-label="Inflammation icon"></div><span>Reduce Inflammation</span></div>
<div class="benefit" style="left:362px;top:3216px"><div class="icon" role="img" aria-label="Joint icon"></div><span>Alleviate Joint Pain</span></div>
<div class="benefit" style="left:615px;top:3216px"><div class="icon" role="img" aria-label="Skin icon"></div><span>Healthier Skin</span></div>
<div class="benefit" style="left:866px;top:3216px"><div class="icon" role="img" aria-label="Longevity icon"></div><span>A Longer &amp; Healthier Life</span></div>

<p class="individual">Specific Improvements will be Individual to You.</p>
<a class="btn btn-dark" style="left:522px;top:3551px;width:156px">Read More <span class="dot"></span></a>

<section class="orange-band" style="top:3673px;height:221px">Everything Works Better With<br>Increased Blood Flow</section>

<h2 class="section-title" style="top:3970px">Our Testimonials</h2>

<svg class="arrow" style="left:56px" width="16" height="26" viewBox="0 0 16 26"><path d="M13 2 3 13l10 11" fill="none" stroke="#222" stroke-width="2.5"/></svg>
<svg class="arrow" style="left:1128px" width="16" height="26" viewBox="0 0 16 26"><path d="M3 2l10 11L3 24" fill="none" stroke="#222" stroke-width="2.5"/></svg>

<div class="quote" style="left:111px;width:316px"><span class="qmark" style="left:12px;top:12px">“</span><p>I climb in my sauna half asleep every morning for 20 minutes before I take a shower and head off to work. It's the only thing I found that really wakes me up in the morning. I'm not a coffee drinker so that's never been an option but this sauna is the perfect morning wake up.</p><span class="qmark" style="right:12px;bottom:0">”</span></div>
<div class="quote" style="left:446px;width:307px"><span class="qmark" style="left:12px;top:12px">“</span><p>I'm only 43 years old with arthritis. The way I move you'd think I was 93. My cold plunge completely rejuvenates my body. It's amazing. It gives me relief unlike any ointment or supplement I've ever taken. I love that it's a natural way to deal with my arthritis that actually works.</p><span class="qmark" style="right:12px;bottom:0">”</span></div>
<div class="quote" style="left:778px;width:309px"><span class="qmark" style="left:12px;top:12px">“</span><p>Having a sauna in my home has been a game-changer. After a long day at work, I step into warmth and it's total relaxation. The heat and gentle steam instantly melts me. It's like a mini vacation without leaving home. I can't imagine life without my sauna.</p><span class="qmark" style="right:12px;bottom:0">”</span></div>
<div class="stars" style="left:219px;width:100px">★★★★★</div>
<div class="stars" style="left:550px;width:100px">★★★★★</div>
<div class="stars" style="left:883px;width:100px">★★★★★</div>

<footer class="site-footer">
  <div class="foot-brand">Maebel Stone Vigor</div>
  <div class="socials"><i></i><i></i><i></i><i></i></div>
  <div class="foot-col" style="left:452px">
    <h5>Quick Links</h5>
    <ul><li>Home</li><li>About Us</li><li>Services</li><li>Gallery</li><li>Testimonials</li></ul>
  </div>
  <div class="foot-col" style="left:676px">
    <h5>Important</h5>
    <ul><li>Terms of Use</li><li>Site Map</li><li>Privacy Policy</li><li>Disclaimer</li></ul>
  </div>
  <div class="foot-col" style="left:881px;width:220px">
    <h5>Contact us</h5>
    <p class="contact-line"><svg width="10" height="14" viewBox="0 0 10 14"><path d="M5 0a5 5 0 0 1 5 5c0 4-5 9-5 9S0 9 0 5a5 5 0 0 1 5-5z" fill="#fff"/><circle cx="5" cy="5" r="2" fill="#1e1e1e"/></svg>39 Lorem ipsum dolor sit amet, consectetur adipiscing elit,</p>
    <p class="contact-line"><svg width="13" height="13" viewBox="0 0 13 13"><path d="M3 0l2 3-1.5 1.5a8 8 0 0 0 5 5L10 8l3 2-1.5 3C5 12.5.5 8 0 1.5z" fill="#fff"/></svg>+1 555 010 0199</p>
    <p class="contact-line"><svg width="14" height="11" viewBox="0 0 14 11"><rect x=".75" y=".75" width="12.5" height="9.5" fill="none" stroke="#fff" stroke-width="1.5"/><path d="M1 1l6 5 6-5" fill="none" stroke="#fff" stroke-width="1.5"/></svg>info@maebelsvigorguys.com</p>
  </div>
  <div class="foot-rule"></div>
  <p class="copyright">Copyright © MaebelsVigorGuys.com 2024 | Allrights Reserved</p>
</footer>

</body>
</html>
```